Redesign of business card for Cedar Ridge Mechanical

We are looking for a new design for our business cards for Cedar Ridge Mechanical. We are a plumbing & HVAC construction company, operating on the West Coast of Canada and USA. Logo attached.
Industry/Entity Type
Construction - Plumbing & HVAC
Contact Information for Business Card
Name, address, phone numbers, email, website address
Look and feel
Each slider illustrates characteristics of the customer's brand and the style your logo design should communicate.

```html
<!DOCTYPE html>
<html lang="en">
<head>
<meta charset="utf-8">
<title>Cedar Ridge Mechanical – Business Card</title>
<link rel="stylesheet" href="https://fonts.googleapis.com/css2?family=Arimo:wght@400&family=Roboto+Condensed:wght@700&display=swap">
<style>
  :root {
    --canvas-bg: #dcd6ce;
    --card-top: #eeebe7;
    --card-bottom: #d3cec8;
    --card-edge: rgba(255, 255, 255, 0.85);
    --ink: #141414;
    --ink-soft: #2a2a2a;
    --divider: #5a5753;
    --band: #0e0e0e;
  }
  * { box-sizing: border-box; margin: 0; padding: 0; }
  html, body {
    width: 1170px;
    height: 1200px;
    overflow: hidden;
    background: var(--canvas-bg);
  }
  .business-card {
    position: absolute;
    left: 85px;
    top: 314px;
    width: 1000px;
    height: 572px;
    border-radius: 26px;
    background: linear-gradient(180deg, var(--card-top) 0%, var(--card-bottom) 100%);
    border: 1.5px solid var(--card-edge);
    box-shadow: 0 18px 40px rgba(60, 50, 40, 0.18);
    overflow: hidden;
    color: var(--ink);
  }
  .brand {
    position: absolute;
    left: 122px;
    top: 222px;
    display: flex;
    align-items: center;
    gap: 16px;
  }
  .brand-square {
    width: 58px;
    height: 58px;
    background: var(--ink);
    flex: none;
  }
  .brand-name {
    font-family: "Roboto Condensed", sans-serif;
    font-weight: 700;
    font-size: 34px;
    line-height: 1.05;
    letter-spacing: 0.5px;
    text-transform: uppercase;
    color: var(--ink);
  }
  .divider {
    position: absolute;
    left: 428px;
    top: 160px;
    width: 2px;
    height: 272px;
    background: var(--divider);
    opacity: 0.7;
  }
  .contact {
    position: absolute;
    left: 458px;
    top: 150px;
    font-family: "Arimo", sans-serif;
  }
  .person-name {
    font-family: "Roboto Condensed", sans-serif;
    font-weight: 700;
    font-size: 38px;
    line-height: 1.1;
    color: var(--ink);
  }
  .person-title {
    font-size: 24px;
    color: var(--ink-soft);
    margin-top: 2px;
  }
  .address {
    font-size: 24px;
    line-height: 32px;
    margin-top: 18px;
    color: var(--ink-soft);
  }
  .channels {
    list-style: none;
    margin-top: 18px;
  }
  .channels li {
    display: flex;
    align-items: center;
    gap: 12px;
    font-size: 24px;
    line-height: 32px;
    color: var(--ink-soft);
  }
  .channels svg {
    width: 22px;
    height: 22px;
    flex: none;
    fill: var(--ink);
  }
  .base-band {
    position: absolute;
    left: 0;
    right: 0;
    bottom: 0;
    height: 18px;
    display: flex;
    gap: 10px;
  }
  .base-band span {
    flex: 1;
    background: var(--band);
  }
</style>
</head>
<body>
  <div class="business-card">
    <div class="brand">
      <div class="brand-square"></div>
      <div class="brand-name">Cedar Ridge<br>Mechanical</div>
    </div>

    <div class="divider"></div>

    <div class="contact">
      <div class="person-name">Daniel Whitford</div>
      <div class="person-title">President</div>
      <div class="address">4127 Harbour View Road<br>Lakeside, NY 11020</div>
      <ul class="channels">
        <li>
          <svg viewBox="0 0 24 24" aria-hidden="true"><path d="M6.6 10.8a15.1 15.1 0 0 0 6.6 6.6l2.2-2.2a1 1 0 0 1 1-.25 11.4 11.4 0 0 0 3.6.57 1 1 0 0 1 1 1V20a1 1 0 0 1-1 1A17 17 0 0 1 3 4a1 1 0 0 1 1-1h3.5a1 1 0 0 1 1 1c0 1.25.2 2.45.57 3.57a1 1 0 0 1-.25 1z"/></svg>
          (555) 2841-7390
        </li>
        <li>
          <svg viewBox="0 0 24 24" aria-hidden="true"><path d="M2 6h20v12H2z M2 6l10 7 10-7" fill="none" stroke="#141414" stroke-width="0"/><path d="M3 7h18v1.2l-9 6-9-6z M3 10.2l9 6 9-6V17H3z"/></svg>
          name@cedarridgemechanical.com
        </li>
        <li>
          <svg viewBox="0 0 24 24" aria-hidden="true"><circle cx="12" cy="12" r="9.5" fill="none" stroke="#141414" stroke-width="2"/><path d="M12 3a9 9 0 0 0 0 18c-2.2-2.5-3.3-5.5-3.3-9S9.8 5.5 12 3z M4 9h16v1.5H4z M4 13.5h16V15H4z"/></svg>
          www.cedarridgemechanical.com
        </li>
      </ul>
    </div>

    <div class="base-band"><span></span><span></span><span></span></div>
  </div>
</body>
</html>
```